Rollaway Stays

We are 100% online, promoting accommodation details and booking facilities for wheelchair dependant travellers.
Listings will only be accommodation providers which meet our specific criteria.

Target Market(s)

Wheelchair dependant people and their companions

Industry/Entity Type

Accommodation

Contact Information for Business Card

Name, mobile phone number, email address, website address

```html
<!DOCTYPE html>
<html lang="en">
<head>
<meta charset="utf-8">
<title>Rollaway Stays – Business Card</title>
<link rel="stylesheet" href="https://fonts.googleapis.com/css2?family=Open+Sans:wght@400;700;800&display=swap">
<style>
  :root {
    --bg: #6f7785;
    --card-dark: #2f2d2e;
    --card-dark-edge: #252324;
    --card-light: #f7f7f7;
    --ink: #2a2a2a;
    --red: #e31b3a;
    --white: #ffffff;
    --muted: #555555;
  }
  * { box-sizing: border-box; margin: 0; padding: 0; }
  html, body { width: 1200px; height: 1024px; overflow: hidden; }
  body {
    background: var(--bg);
    font-family: "Open Sans", Arial, sans-serif;
    display: flex;
    flex-direction: column;
    align-items: center;
    justify-content: center;
    gap: 60px;
  }
  .card {
    position: relative;
    width: 740px;
    height: 420px;
    border-radius: 26px;
    overflow: hidden;
  }
  /* Front */
  .card--front {
    background: radial-gradient(ellipse at 50% 40%, #3d3b3c 0%, var(--card-dark) 60%, var(--card-dark-edge) 100%);
    color: var(--white);
  }
  .brand {
    display: flex;
    align-items: center;
    gap: 14px;
  }
  .brand__dot {
    width: 34px; height: 34px;
    border-radius: 50%;
    background: var(--red);
  }
  .brand__name {
    font-weight: 800;
    font-size: 46px;
    letter-spacing: -0.5px;
    color: var(--red);
    line-height: 1;
  }
  .card--front .brand {
    position: absolute;
    left: 50%; top: 150px;
    transform: translateX(-50%);
  }
  .card--front .site {
    position: absolute;
    left: 0; right: 0; top: 260px;
    text-align: center;
    font-size: 19px;
    letter-spacing: 0.3px;
  }
  /* Back */
  .card--back {
    background: radial-gradient(ellipse at 40% 40%, var(--white) 0%, var(--card-light) 65%, #e9e9e9 100%);
    color: var(--ink);
  }
  .card--back .brand {
    position: absolute;
    left: 44px; top: 50px;
  }
  .card--back .brand__name { font-size: 40px; }
  .card--back .brand__dot { width: 28px; height: 28px; }
  .holder {
    position: absolute;
    left: 44px; top: 168px;
    font-weight: 700;
    font-size: 26px;
    letter-spacing: 0.2px;
  }
  .rule {
    position: absolute;
    left: 44px; right: 40px; top: 214px;
    height: 1px;
    background: var(--ink);
  }
  .rule::before {
    content: "";
    position: absolute;
    left: 0; top: -1px;
    width: 150px; height: 3px;
    background: var(--red);
  }
  .contacts {
    position: absolute;
    right: 40px; top: 238px;
    list-style: none;
    font-size: 19px;
    line-height: 1.45;
    color: var(--ink);
  }
  .contacts li { display: flex; align-items: center; gap: 10px; }
  .contacts svg { width: 14px; height: 14px; flex: none; fill: var(--red); }
  .edge-band {
    position: absolute;
    left: 0; right: 0; bottom: 0;
    height: 34px;
    display: flex;
  }
  .edge-band__red { width: 28%; background: var(--red); }
  .edge-band__dark { flex: 1; background: var(--card-dark); }
</style>
</head>
<body>

  <section class="card card--front" aria-label="Card front">
    <div class="brand">
      <span class="brand__dot"></span>
      <span class="brand__name">Rollaway Stays</span>
    </div>
    <p class="site">www.rollawaystays.example</p>
  </section>

  <section class="card card--back" aria-label="Card back">
    <div class="brand">
      <span class="brand__dot"></span>
      <span class="brand__name">Rollaway Stays</span>
    </div>
    <h1 class="holder">Alex Carter</h1>
    <div class="rule"></div>
    <ul class="contacts">
      <li>
        <svg viewBox="0 0 14 14" aria-hidden="true"><rect x="3" y="0" width="8" height="14" rx="1.5"/><rect x="4.5" y="2" width="5" height="8" fill="#fff"/></svg>
        555-013-2468
      </li>
      <li>
        <svg viewBox="0 0 14 14" aria-hidden="true"><rect x="0" y="2" width="14" height="10" rx="1"/><path d="M1 3 L7 8 L13 3" stroke="#fff" stroke-width="1.4" fill="none"/></svg>
        hello@rollawaystays.example
      </li>
      <li>
        <svg viewBox="0 0 14 14" aria-hidden="true"><circle cx="7" cy="7" r="7"/><path d="M0 7 H14 M7 0 C3 4 3 10 7 14 M7 0 C11 4 11 10 7 14" stroke="#fff" stroke-width="1" fill="none"/></svg>
        www.rollawaystays.example
      </li>
    </ul>
    <div class="edge-band">
      <span class="edge-band__red"></span>
      <span class="edge-band__dark"></span>
    </div>
  </section>

</body>
</html>
```